Private Investment Firm Needs PowerPoint Presentation Template

Design PowerPoint template, take Pinebrook-submitted rough presentation draft, and drop it into new template. See attached Project Brief file for more detail.
Updates

Some decent designs have been submitted but they seem to lack the understanding of our target markets. I am hopeful that more time and feedback will result in better results.

Target Market(s)

Private company owners and intermediaries.

Font styles to use
Serif

Colors
3176b5

Requirements
Must have
• See attached Project Brief.
Nice to have
Should not have
• No B2C fluff--this is a B2B project.

```html
<!DOCTYPE html>
<html lang="en">
<head>
<meta charset="utf-8">
<title>Pinebrook Capital – Contact</title>
<link rel="stylesheet" href="https://fonts.googleapis.com/css2?family=Montserrat:wght@400;600;700&display=swap">
<style>
  :root {
    --brand-blue: #3176b5;
    --deep-blue: #1e66ad;
    --light-blue: #3d90d2;
    --heading-blue: #1b5ea6;
    --body-grey: #555a60;
    --slash-grey: #4a4a4a;
    --page-bg: #ecebe8;
    --slide-top: #ffffff;
    --slide-bottom: #eceded;
    --white: #ffffff;
  }
  * { box-sizing: border-box; margin: 0; padding: 0; }
  html, body {
    width: 1200px; height: 770px; overflow: hidden;
    background: var(--page-bg);
    font-family: "Montserrat", Arial, sans-serif;
  }
  .slide {
    position: absolute; left: 0; top: 48px;
    width: 1200px; height: 675px; overflow: hidden;
    background: linear-gradient(160deg, var(--slide-top) 0%, var(--slide-bottom) 100%);
    box-shadow: 0 6px 14px rgba(0,0,0,0.25);
  }
  .slide-shapes { position: absolute; inset: 0; }
  .slide-title {
    position: absolute; left: 435px; top: 40px; width: 310px; height: 51px;
    display: flex; align-items: center; justify-content: center;
    color: var(--white); font-size: 41px; font-weight: 400; letter-spacing: 1px;
  }
  .timeline-line {
    position: absolute; left: 114px; top: 144px; width: 1px; height: 440px;
    background: #9aa0a6;
  }
  .contact {
    position: absolute; left: 154px;
    color: var(--body-grey); font-size: 21px; line-height: 23.4px;
  }
  .contact::before {
    content: ""; position: absolute; left: -49px; top: 2px;
    width: 18px; height: 18px; border-radius: 50%;
    border: 1.5px solid var(--heading-blue); background: var(--white);
  }
  .contact::after {
    content: ""; position: absolute; left: -44px; top: 7px;
    width: 8px; height: 8px; border-radius: 50%;
    background: var(--heading-blue);
  }
  .contact-name {
    color: var(--heading-blue); font-weight: 700; font-size: 22px;
    line-height: 26px; margin-bottom: 4px;
  }
  .contact-name.office { margin-bottom: 8px; }
  .contact .phone { color: var(--brand-blue); }
  .contact .domain, .website .domain { color: var(--heading-blue); font-weight: 700; }
  .contact.person { top: 133px; }
  .contact.boston { top: 329px; }
  .contact.sanfrancisco { top: 482px; }
  .website {
    position: absolute; left: 114px; top: 624px;
    font-size: 18px; color: #333;
  }
  .portrait {
    position: absolute; left: 862px; top: 257px; width: 260px; height: 260px;
    border-radius: 50%; border: 4px solid var(--white);
    background: radial-gradient(circle at 50% 35%, #c9d3df 0%, #a9b6c6 45%, #2a3346 80%);
  }
  .brand {
    position: absolute; left: 878px; top: 592px;
    display: flex; align-items: center; gap: 12px;
    color: var(--white); font-size: 26px; font-weight: 600; letter-spacing: 2px;
  }
  .brand-dot { width: 34px; height: 34px; border-radius: 50%; background: var(--white); }
  .page-number {
    position: absolute; left: 1147px; top: 634px;
    color: var(--white); font-size: 11px; font-weight: 700;
  }
</style>
</head>
<body>
  <main class="slide">
    <svg class="slide-shapes" width="1200" height="675" viewBox="0 0 1200 675">
      <defs>
        <linearGradient id="corner-fill" x1="0" y1="1" x2="1" y2="0">
          <stop offset="0" stop-color="#3a8fd1"/>
          <stop offset="1" stop-color="#1d66ad"/>
        </linearGradient>
      </defs>
      <polygon class="corner-top-left" points="0,0 150,0 0,169" fill="var(--deep-blue)"/>
      <polygon class="corner-bottom-right" points="1200,98 1200,675 685,675" fill="url(#corner-fill)"/>
      <g class="title-banner">
        <polygon points="420,40 432,40 419,91 407,91" fill="var(--slash-grey)"/>
        <polygon points="448,40 757,40 744,91 435,91" fill="var(--deep-blue)"/>
        <polygon points="763,40 775,40 762,91 750,91" fill="var(--slash-grey)"/>
      </g>
    </svg>

    <h1 class="slide-title">CONTACT</h1>

    <div class="timeline-line"></div>

    <section class="contact person">
      <h2 class="contact-name">Daniel R. Ashford</h2>
      <p>Principal<br>
      410 Meadowlark Lane, Suite 210<br>
      Ridgefield, CT&nbsp; 06877<br>
      Direct: (555) 014-2271<br>
      dashford@<span class="domain">pinebrookcapital</span>.com</p>
    </section>

    <section class="contact boston">
      <h2 class="contact-name office">Boston Office</h2>
      <p>18 Harbor Point Drive, Suite 300<br>
      Beverly, MA 01915<br>
      <span class="phone">(555) 014-2200</span></p>
    </section>

    <section class="contact sanfrancisco">
      <h2 class="contact-name">San Francisco Office</h2>
      <p>240 Market Lane, Suite 800<br>
      San Francisco, CA 94111<br>
      <span class="phone">(555) 013-4400</span></p>
    </section>

    <p class="website">www.<span class="domain">pinebrookcapital</span>.com</p>

    <div class="portrait" role="img" aria-label="Portrait photo of the principal in a dark suit, arms crossed"></div>

    <div class="brand"><span class="brand-dot"></span>PINEBROOK CAPITAL</div>

    <span class="page-number">4.</span>
  </main>
</body>
</html>
```